Business Cards - Brightpath Horizon

need to design unique business card for my mortgage business. I need to design credit card style business card for my business or any unique idea that you might have

Target Market(s)

Home Loan customers

Industry/Entity Type

Mortgage Brokerage

Contact Information for Business Card

please design credit card style or very unique style business card

Colors

Designer to choose colors to be used in the design.

Requirements
Must have
• Name
• position
• Phone number
• fax number
• email address
• website address
• social media address
• All above fields will be provided once design in finalised

```html
<!DOCTYPE html>
<html lang="en">
<head>
<meta charset="utf-8">
<title>Brightpath Horizon – Business Card</title>
<link rel="stylesheet" href="https://fonts.googleapis.com/css2?family=Tinos:ital,wght@0,400;0,700;1,400&family=Share+Tech+Mono&display=swap">
<style>
  :root {
    --page-bg: #e6e6e4;
    --card-bg: #1b1c1e;
    --card-edge: #232427;
    --brand-blue: #1d45e0;
    --brand-orange: #f0962a;
    --text-light: #e9e9e9;
    --tree-tone: #1f3940;
    --emboss-tone: #26272a;
  }
  * { box-sizing: border-box; margin: 0; padding: 0; }
  html, body {
    width: 1200px; height: 901px; overflow: hidden;
    background: var(--page-bg);
  }
  .business-card {
    position: absolute; left: 70px; top: 117px;
    width: 1060px; height: 666px;
    background: linear-gradient(160deg, var(--card-edge), var(--card-bg) 60%);
    border-radius: 10px;
    overflow: hidden;
    box-shadow: 0 12px 30px rgba(0,0,0,.25);
    font-family: "Tinos", "Times New Roman", serif;
  }
  .tree-decoration {
    position: absolute; left: 600px; top: 0; width: 460px; height: 666px;
    background: radial-gradient(ellipse 55% 45% at 45% 38%, var(--tree-tone), rgba(31,57,64,.55) 60%, transparent 100%);
  }
  .houses-emboss {
    position: absolute; left: 0; top: 455px; width: 850px; height: 211px;
    background: linear-gradient(180deg, transparent, var(--emboss-tone) 45%);
  }
  .holder-name {
    position: absolute; left: 58px; top: 76px;
    color: var(--brand-blue); font-size: 34px; font-weight: 400;
    letter-spacing: 1px; line-height: 1;
  }
  .holder-role {
    position: absolute; left: 58px; top: 125px;
    color: var(--brand-orange); font-size: 27px; line-height: 1;
  }
  .card-number {
    position: absolute; left: 56px; top: 186px;
    color: var(--brand-blue); font-family: "Share Tech Mono", monospace;
    font-size: 64px; letter-spacing: 4px; line-height: 1; white-space: nowrap;
  }
  .contact-list { position: absolute; left: 62px; top: 292px; list-style: none; }
  .contact-item {
    display: flex; align-items: center; gap: 14px;
    height: 38px; color: var(--text-light); font-size: 26px;
  }
  .contact-icon { width: 24px; height: 24px; fill: var(--brand-blue); flex: none; }
  .social-row { position: absolute; left: 58px; top: 418px; display: flex; gap: 6px; }
  .social-dot {
    width: 46px; height: 46px; border-radius: 50%;
    background: var(--brand-blue);
  }
  .brand {
    position: absolute; left: 700px; top: 86px; width: 330px;
    display: flex; align-items: center; gap: 14px;
  }
  .brand-mark { width: 40px; height: 40px; border-radius: 50%; background: var(--brand-blue); flex: none; }
  .brand-name { color: var(--brand-blue); font-size: 44px; line-height: 1.05; }
  .brand-tagline {
    position: absolute; left: 740px; top: 244px;
    color: var(--brand-orange); font-style: italic; font-size: 24px; white-space: nowrap;
  }
</style>
</head>
<body>
  <div class="business-card">
    <div class="tree-decoration" role="img" aria-label="Large faint tree silhouette decoration"></div>
    <div class="houses-emboss" role="img" aria-label="Embossed row of house rooftops"></div>

    <h1 class="holder-name">DANIEL REYES</h1>
    <p class="holder-role">CEO/FOUNDER</p>
    <p class="card-number">415 273 8096</p>

    <ul class="contact-list">
      <li class="contact-item">
        <svg class="contact-icon" viewBox="0 0 24 24"><rect x="4" y="3" width="13" height="6" rx="1"/><rect x="2" y="9" width="20" height="10" rx="2"/><rect x="6" y="15" width="12" height="6" fill="#1b1c1e"/></svg>
        <span>415 273 8097</span>
      </li>
      <li class="contact-item">
        <svg class="contact-icon" viewBox="0 0 24 24"><rect x="2" y="5" width="20" height="14" rx="2"/><path d="M3 6l9 7 9-7" stroke="#1b1c1e" stroke-width="2" fill="none"/></svg>
        <span>daniel@brightpathhz.com</span>
      </li>
      <li class="contact-item">
        <svg class="contact-icon" viewBox="0 0 24 24"><circle cx="12" cy="12" r="10"/><path d="M2 12h20M12 2c4 4 4 16 0 20M12 2c-4 4-4 16 0 20" stroke="#1b1c1e" stroke-width="1.6" fill="none"/></svg>
        <span>www.brightpathhz.com</span>
      </li>
    </ul>

    <div class="social-row">
      <span class="social-dot"></span>
      <span class="social-dot"></span>
      <span class="social-dot"></span>
      <span class="social-dot"></span>
    </div>

    <div class="brand">
      <span class="brand-mark"></span>
      <span class="brand-name">BRIGHTPATH HORIZON</span>
    </div>
    <p class="brand-tagline">Sound choice, Smart timing</p>
  </div>
</body>
</html>
```